Automotive component supplier needs a business card design

We need a business card design for our company called Velran Global Components Ltd based in the UK. We are a supplier of interior and exterior components to premium car manufacturers such as Corvel Ashby, Hadley Fenn, Marquist and Tavarelli. We would like to see a modern business card design that uses the colour blue.

Target Market(s)

Premium automotive car manufacturers.

Industry/Entity Type

Automotive

Contact Information for Business Card

Company Name : Velran Global Components Limited
Address: 17 Marlow Yard, Upper Heath, Warwick, CV31 8QL, United Kingdom
Web Address : www.velrancomponents-example.co.uk

Font styles to use
Other font styles liked:
• Helvetica

Colors
3176b5
0255a3
85acd3
cfdeed
cee9f5
85cae6
34a6d7
0692cd
9bcb3c

Requirements
Must have
• Clear company logo and a mixture of blue colours.
Nice to have
• A high quality modern image.
Should not have
• Multiple colours.

```html
<!DOCTYPE html>
<html lang="en">
<head>
<meta charset="utf-8">
<title>Velran Global Components – Business Card</title>
<link href="https://fonts.googleapis.com/css2?family=Roboto:wght@400;700&display=swap" rel="stylesheet">
<style>
  :root {
    --stage: #202020;
    --brand-blue: #0692cd;
    --accent-green: #9bcb3c;
    --card-white: #ffffff;
    --text-grey: #555a5e;
  }
  * { margin: 0; padding: 0; box-sizing: border-box; }
  html, body {
    width: 1200px; height: 987px; overflow: hidden;
    background: var(--stage);
    font-family: "Roboto", Helvetica, Arial, sans-serif;
  }
  .card {
    position: absolute; left: 293px; width: 615px; height: 352px;
    box-shadow: 0 4px 14px rgba(0,0,0,0.45);
  }
  .card-front { top: 130px; background: var(--card-white); }
  .card-back { top: 505px; background: var(--brand-blue); }

  .brand {
    position: absolute; display: flex; align-items: center; gap: 10px;
    font-weight: 700; text-transform: uppercase; letter-spacing: 0.5px;
  }
  .brand-mark { width: 12px; height: 12px; background: var(--accent-green); }
  .card-front .brand { left: 39px; top: 44px; font-size: 26px; color: var(--brand-blue); }
  .card-back .brand {
    left: 0; right: 0; top: 150px; justify-content: center;
    font-size: 34px; color: var(--card-white);
  }
  .card-back .brand-mark { width: 14px; height: 14px; }

  .person-name {
    position: absolute; left: 39px; top: 145px;
    font-size: 21px; font-weight: 700; color: var(--brand-blue); text-transform: uppercase;
  }
  .person-role {
    position: absolute; left: 39px; top: 173px;
    font-size: 15px; color: var(--accent-green);
  }
  .address {
    position: absolute; left: 39px; top: 203px;
    font-size: 15px; line-height: 23px; color: var(--text-grey); font-style: normal;
  }
  .contact-list {
    position: absolute; left: 39px; top: 256px; list-style: none;
    font-size: 15px; color: var(--text-grey);
  }
  .contact-list li { display: flex; align-items: center; gap: 7px; height: 24px; }
  .contact-list svg { width: 14px; height: 14px; fill: var(--brand-blue); flex: none; }

  .web-strip {
    position: absolute; right: 0; top: 0; width: 40px; height: 316px;
    background: var(--brand-blue);
    display: flex; align-items: center; justify-content: center;
  }
  .web-strip span {
    writing-mode: vertical-rl; transform: rotate(180deg);
    color: var(--card-white); font-size: 12.5px; letter-spacing: 1.2px;
  }
  .corner-tab {
    position: absolute; right: 6px; top: 322px; width: 30px; height: 25px;
    background: var(--accent-green); border-radius: 4px;
  }
</style>
</head>
<body>
  <section class="card card-front">
    <div class="brand"><span>Velran Global Components</span><span class="brand-mark"></span></div>
    <div class="person-name">Daniel Hartwell</div>
    <div class="person-role">CEO/Founder</div>
    <address class="address">17 Marlow Yard, Upper Heath<br>Warwick, CV31 8QL, United Kingdom</address>
    <ul class="contact-list">
      <li>
        <svg viewBox="0 0 24 24" aria-hidden="true"><path d="M6.6 10.8a15.1 15.1 0 0 0 6.6 6.6l2.2-2.2c.3-.3.7-.4 1-.2 1.1.4 2.3.6 3.6.6.6 0 1 .4 1 1V20c0 .6-.4 1-1 1A17 17 0 0 1 3 4c0-.6.4-1 1-1h3.5c.6 0 1 .4 1 1 0 1.3.2 2.5.6 3.6.1.3 0 .7-.2 1z"/></svg>
        610 555 0147
      </li>
      <li>
        <svg viewBox="0 0 24 24" aria-hidden="true"><path d="M7 1h10a2 2 0 0 1 2 2v18a2 2 0 0 1-2 2H7a2 2 0 0 1-2-2V3a2 2 0 0 1 2-2zm0 3v14h10V4zm5 15.5a1.2 1.2 0 1 0 0 2.4 1.2 1.2 0 0 0 0-2.4z"/></svg>
        820 555 0193
      </li>
      <li>
        <svg viewBox="0 0 24 24" aria-hidden="true"><path d="M2 5h20v14H2zm2 2v.4l8 5.2 8-5.2V7zm0 2.8V17h16V9.8l-8 5.2z"/></svg>
        daniel@velrancomponents-example.co.uk
      </li>
    </ul>
    <div class="web-strip"><span>www.velrancomponents-example.co.uk</span></div>
    <div class="corner-tab"></div>
  </section>

  <section class="card card-back">
    <div class="brand"><span>Velran Global Components</span><span class="brand-mark"></span></div>
  </section>
</body>
</html>
```